Veltrane Group Business Card Design

The CEO is looking for a new trendy look for his business card.
You can stay with current branding or come up with something new/creative. It can be 3D, including Medical Office buildings. You can use our logo in a variety of colors. Please include name, title, company name, company website, email address, cell number

Target Market(s)

Real Estate Development and Construction

Industry/Entity Type

Health care real estate

Contact Information for Business Card

Rohesh Kamdar, CEO M-604.781.2249 E-roheshkamdar@veltrane.com Address:4180 Lindqvist Ave, Tampa, FL 33482 www.veltrane.com

Font styles to use
Other font styles liked:
• Be creative

Requirements
Must have
• Creative, trendy look
Nice to have
• Please go to our website to get a feel- www. veltrane.com
Should not have
• small fonts

```html
<!DOCTYPE html>
<html lang="en">
<head>
<meta charset="utf-8">
<title>Veltrane Group Business Card</title>
<link href="https://fonts.googleapis.com/css2?family=Lato:wght@400;700;900&display=swap" rel="stylesheet">
<style>
  :root {
    --bg: #3a3a3a;
    --navy: #1f3356;
    --red: #b01e2a;
    --white: #ffffff;
    --ink: #1f3356;
  }
  * { margin: 0; padding: 0; box-sizing: border-box; }
  html, body { width: 1200px; height: 689px; overflow: hidden; }
  body {
    background: var(--bg);
    font-family: "Lato", sans-serif;
    display: flex;
    align-items: center;
    justify-content: center;
    gap: 48px;
  }
  .card {
    width: 540px;
    height: 310px;
    border-radius: 18px;
    overflow: hidden;
    position: relative;
    box-shadow: 0 14px 30px rgba(0,0,0,.45);
  }
  .card-front {
    background: var(--white);
    display: flex;
    align-items: center;
    justify-content: center;
  }
  .wordmark {
    font-family: "Lato", sans-serif;
    font-weight: 900;
    color: var(--red);
    letter-spacing: -1px;
    white-space: nowrap;
  }
  .card-front .wordmark { font-size: 52px; }
  .card-back { background: var(--navy); }
  .back-logo {
    position: absolute;
    left: 0; top: 0;
    width: 225px; height: 100%;
    display: flex;
    align-items: center;
    justify-content: center;
    padding-top: 90px;
  }
  .back-logo .wordmark { font-size: 30px; }
  .info-panel {
    position: absolute;
    left: 225px; top: 0;
    width: 278px; height: 100%;
    background: var(--white);
  }
  .name-band {
    position: absolute;
    left: 225px; top: 40px;
    width: 315px; height: 66px;
    background: var(--red);
    color: var(--white);
    padding: 11px 0 0 24px;
  }
  .name {
    font-weight: 900;
    font-size: 26px;
    letter-spacing: 1px;
    line-height: 1.05;
  }
  .title {
    font-weight: 400;
    font-size: 14px;
    letter-spacing: .5px;
    margin-top: 3px;
  }
  .contact-list {
    position: absolute;
    left: 249px; top: 126px;
    list-style: none;
    color: var(--ink);
    font-size: 13.5px;
    line-height: 1.45;
  }
  .contact-list li {
    display: flex;
    align-items: flex-start;
    gap: 10px;
  }
  .contact-list svg {
    width: 13px; height: 13px;
    flex: none;
    margin-top: 3px;
    fill: var(--red);
  }
  .contact-list .address { margin-bottom: 4px; }
</style>
</head>
<body>
  <div class="card card-front">
    <span class="wordmark">Veltrane Group</span>
  </div>

  <div class="card card-back">
    <div class="back-logo">
      <span class="wordmark">Veltrane Group</span>
    </div>
    <div class="info-panel"></div>
    <div class="name-band">
      <div class="name">ROHESH KAMDAR</div>
      <div class="title">President / CEO</div>
    </div>
    <ul class="contact-list">
      <li class="address">
        <svg viewBox="0 0 12 12"><path d="M6 0a4 4 0 0 0-4 4c0 3 4 8 4 8s4-5 4-8a4 4 0 0 0-4-4zm0 5.5A1.5 1.5 0 1 1 6 2.5a1.5 1.5 0 0 1 0 3z"/></svg>
        <span>4180 Lindqvist Ave<br>Tampa, FL 33482</span>
      </li>
      <li>
        <svg viewBox="0 0 12 12"><path d="M3 0h6a1 1 0 0 1 1 1v10a1 1 0 0 1-1 1H3a1 1 0 0 1-1-1V1a1 1 0 0 1 1-1zm.5 1.5v7.5h5V1.5z"/></svg>
        <span>604.781.2249</span>
      </li>
      <li>
        <svg viewBox="0 0 12 12"><path d="M0 2h12v8H0zm1 1v.4l5 3.4 5-3.4V3z"/></svg>
        <span>roheshkamdar@veltrane.com</span>
      </li>
      <li>
        <svg viewBox="0 0 12 12"><path d="M6 0a6 6 0 1 0 0 12A6 6 0 0 0 6 0zm0 1.2c.8 0 1.6 1.8 1.8 4.2H4.2C4.4 3 5.2 1.2 6 1.2zM4.2 6.6h3.6C7.6 9 6.8 10.8 6 10.8S4.4 9 4.2 6.6z"/></svg>
        <span>www.veltrane.com</span>
      </li>
    </ul>
  </div>
</body>
</html>
```